Healthcare Service Provider looking for PowerPoint Template

BMV Profile of the company & business activity
===================================
BMV is the leading after-sale healthcare services provider in Kuwait. The IT department in the company sells & executes Healthcare IT projects in hospitals that mainly cover:

1. IT Infrastructure covering data center, disaster recovery, servers, virtualization, backup, redundancy & high-availability, multi-site connectivity, wired & wireless networking, OS & network management, software subscriptions, …etc.

2. Healthcare IT systems covering the Hospital Management system, Electronic Medical Record, evidence-based clinical content, clinical decision support systems, Radiology information system, Lab information system, pharmacy management system, ICU system, dental system, dietary & nutrition system, integration with 3rd party systems in the hospital

3. Human resources covering the company specialized teams of clinical informatics specialists, pharmacists, nurses, project managers, user experience specialists, integration specialists, systems analysts, systems developers, DB administrators, Network administrators, system architects, systems engineers, …

The assortment of these professionals handle the services for implementing specialty Healthcare IT systems, training hospital staff & healthcare professionals, on-site support & maintenance of implemented healthcare systems at the hospital

Requested design job
================
We require a PowerPoint template to be used by the IT department in presenting sales & marketing pitches, commercial proposals, projects, and related to the business activities described in the profile.

The design of the PowerPoint template should:

. be personalized for the business activities of the IT department. promote the corporate brand identity of the company. provide clean, modern and fluent look & feel for presenting on screen, projector or printing. include font selection & design as part of the template design. light colored background

. multiple page layouts & slide types like a cover slide, title slide, different types of content slides, ….

. include design collaterals like icons and clip-arts

. have common design elements in PowerPoint Master slides

Included are the current corporate logos of the company.

In summary, simplicity, fluency and personality are key to the design we seek.

Requirements
Must have
• The design of the PowerPoint template should:
• . be personalized for the business activities of the IT department. promote the corporate brand identity of the company. provide clean, modern and fluent look & feel for presenting on screen, projector or printing. include font selection & design as part of the template design. light colored background
• . multiple page layouts & slide types like a cover slide, title slide, different types of content slides, ….
• . include design collaterals like icons and clip-arts
• . have common design elements in PowerPoint Master slides

```html
<!DOCTYPE html>
<html lang="en">
<head>
<meta charset="utf-8">
<title>BMV Healthcare IT Presentation Template</title>
<link href="https://fonts.googleapis.com/css2?family=Ubuntu:wght@300;400;500;700&display=swap" rel="stylesheet">
<style>
:root{
  --canvas:#e9eaec;
  --slide:#ffffff;
  --navy:#1d2842;
  --rule:#d3d6da;
  --kicker:#a2a7ae;
  --body:#80868d;
  --footer:#f4f4f5;
  --pill:#d6d8db;
  --photo-a:#93a8b3;
  --photo-b:#6d8592;
}
*{margin:0;padding:0;box-sizing:border-box}
html,body{width:1200px;height:1200px;overflow:hidden;background:var(--canvas)}
body{font-family:"Ubuntu",sans-serif}
.stage{position:absolute;left:0;top:0;width:1500px;height:1500px;transform:scale(.8);transform-origin:0 0}
.slide{position:absolute;width:545px;height:308px;background:var(--slide);overflow:hidden;box-shadow:0 2px 6px rgba(0,0,0,.04)}
.photo{position:absolute;background:linear-gradient(135deg,var(--photo-a),var(--photo-b))}
.rule{position:absolute;top:0;width:1px;background:var(--rule)}
.accent{position:absolute;width:3px;height:28px;background:var(--navy)}
.title{position:absolute;line-height:15px}
.title .kicker{display:block;font-size:15px;font-weight:300;color:var(--kicker)}
.title .main{display:block;font-size:16px;font-weight:700;color:var(--navy)}
.copy{position:absolute;font-size:6px;line-height:12.7px;color:var(--body)}
.copy p+p{margin-top:0}
.footer{position:absolute;bottom:0;height:22px;background:var(--footer)}
.brand{position:absolute;left:28px;top:5px;display:flex;align-items:center;gap:4px}
.brand b{font-size:10px;font-weight:700;color:var(--navy)}
.brand small{font-size:3.2px;color:var(--navy);line-height:4px;width:58px}
.partner{position:absolute;left:127px;top:4px;display:flex;align-items:center;gap:3px;font-size:8px;font-weight:500;color:var(--navy)}
.partner i{width:13px;height:13px;border-radius:50%;border:2px solid var(--navy)}
.pill{position:absolute;right:17px;top:7px;width:20px;height:8px;border-radius:4px;background:var(--pill);color:#fff;font-size:5.5px;text-align:center;line-height:8px}
.card{position:absolute;text-align:center;color:var(--body);font-size:5.5px;line-height:10px}
.card h4{font-size:8.5px;font-weight:500;color:var(--navy);margin-bottom:3px;line-height:11px}
.card.raised{background:#fff;box-shadow:0 4px 14px rgba(0,0,0,.14);padding-top:30px}
.feature{position:absolute;top:90px;width:110px;margin-left:-55px;text-align:center}
.feature svg{display:block;margin:0 auto}
.feature h4{font-size:14px;font-weight:500;color:var(--navy);margin-top:2px}
.feature p{font-size:6px;line-height:12.7px;color:var(--body);margin-top:4px;text-align:left;padding-left:6px}
</style>
</head>
<body>
<div class="stage">

<!-- Slide: stats collage -->
<section class="slide" style="left:240px;top:69px">
  <div class="rule" style="left:30px;height:140px"></div>
  <div class="accent" style="left:29px;top:74px"></div>
  <div class="title" style="left:41px;top:71px"><span class="kicker">Place for the</span><span class="main">Slide Title</span></div>
  <div class="copy" style="left:43px;top:110px;width:268px">We plan, build and support clinical systems for hospitals across the region. Our teams cover data centers, networks, medical records, lab and pharmacy software, with on-site training and care for every install. Each project follows clear steps from first review to final handover, and we stay close after go-live.</div>
  <svg style="position:absolute;left:0;top:0" width="545" height="308" viewBox="0 0 545 308">
    <defs><linearGradient id="ph" x1="0" y1="0" x2="1" y2="1"><stop offset="0" stop-color="#93a8b3"/><stop offset="1" stop-color="#6d8592"/></linearGradient></defs>
    <g role="img" aria-label="Photo collage of a clinician taking blood pressure and filling a report">
      <rect x="-46" y="-46" width="92" height="92" fill="url(#ph)" transform="translate(388 130) rotate(45)"/>
      <rect x="-30" y="-30" width="60" height="60" fill="url(#ph)" transform="translate(510 78) rotate(45)"/>
      <rect x="-44" y="-44" width="88" height="88" fill="url(#ph)" transform="translate(480 212) rotate(45)"/>
    </g>
    <rect x="-33" y="-33" width="66" height="66" fill="#f1f2f3" transform="translate(470 108) rotate(45)"/>
    <text x="470" y="108" text-anchor="middle" font-family="Ubuntu,sans-serif" font-size="14" font-weight="500" fill="#6b717a">1000</text>
    <text x="470" y="118" text-anchor="middle" font-family="Ubuntu,sans-serif" font-size="7" fill="#8d9299">Projects</text>
    <rect x="-33" y="-33" width="66" height="66" fill="#f1f2f3" transform="translate(378 200) rotate(45)"/>
    <text x="378" y="200" text-anchor="middle" font-family="Ubuntu,sans-serif" font-size="14" font-weight="500" fill="#6b717a">430</text>
    <text x="378" y="210" text-anchor="middle" font-family="Ubuntu,sans-serif" font-size="7" fill="#8d9299">Clients</text>
  </svg>
  <div class="footer" style="left:0;width:545px">
    <div class="brand"><b>BMV</b><small>Bright Medical Ventures</small></div>
    <div class="partner"><i></i>PARTNER LOGO</div>
    <div class="pill">01</div>
  </div>
</section>

<!-- Slide: photo left -->
<section class="slide" style="left:825px;top:69px">
  <div class="photo" style="left:0;top:0;width:200px;height:308px" role="img" aria-label="Photo of a hand writing on a daily report clipboard beside a syringe tray"></div>
  <div class="rule" style="left:261px;height:250px"></div>
  <div class="accent" style="left:260px;top:78px"></div>
  <div class="title" style="left:278px;top:76px"><span class="kicker">Place for the</span><span class="main">Slide Title</span></div>
  <div class="copy" style="left:278px;top:122px;width:236px">We plan, build and support clinical systems for hospitals across the region. Our teams cover data centers, networks, medical records, lab and pharmacy software, with on-site training and care for every install. Each project follows clear steps from first review to final handover, and we stay close after go-live.</div>
  <div class="footer" style="left:200px;width:345px">
    <div class="pill">01</div>
  </div>
</section>

<!-- Slide: grid of services -->
<section class="slide" style="left:240px;top:421px">
  <div class="rule" style="left:26px;height:100px"></div>
  <div class="accent" style="left:25px;top:76px"></div>
  <div class="title" style="left:38px;top:73px"><span class="kicker">Place for the</span><span class="main">Slide Title</span></div>
  <div class="copy" style="left:38px;top:119px;width:152px">We plan, build and support clinical systems for hospitals across the region. Our teams cover data centers, networks, medical records, lab and pharmacy software, with on-site training and care for every install. Each project follows clear steps from first review to final handover, and we stay close after go-live.</div>
  <div class="photo" style="left:284px;top:0;width:130px;height:96px" role="img" aria-label="Photo of a blood pressure check"></div>
  <div class="card" style="left:430px;top:26px;width:100px"><h4>Your Title</h4>Short note on this service for hospital teams.</div>
  <div class="photo" style="left:421px;top:102px;width:124px;height:102px" role="img" aria-label="Photo of a report beside a laptop keyboard"></div>
  <div class="photo" style="left:284px;top:210px;width:130px;height:98px" role="img" aria-label="Photo of medical tools and a clipboard on a desk"></div>
  <div class="card" style="left:430px;top:226px;width:100px"><h4>Your Title</h4>Short note on this service for hospital teams.</div>
  <div class="card raised" style="left:276px;top:96px;width:144px;height:114px;padding-left:20px;padding-right:20px"><h4>Your Title</h4>Short note on this service for hospital teams.</div>
  <div class="footer" style="left:0;width:284px">
    <div class="brand"><b>BMV</b><small>Bright Medical Ventures</small></div>
    <div class="partner"><i></i>PARTNER LOGO</div>
  </div>
</section>

<!-- Slide: photo right -->
<section class="slide" style="left:825px;top:421px">
  <div class="rule" style="left:30px;height:210px"></div>
  <div class="accent" style="left:29px;top:71px"></div>
  <div class="title" style="left:41px;top:69px"><span class="kicker">Place for the</span><span class="main">Slide Title</span></div>
  <div class="copy" style="left:44px;top:108px;width:136px">We plan, build and support clinical systems for hospitals across the region. Our teams cover data centers, networks, medical records, lab and pharmacy software, with on-site training and care for every install. Each project follows clear steps from first review to final handover, and we stay close after go-live. Support staff remain on call to keep every system stable, safe and ready for daily clinical work.</div>
  <div class="photo" style="left:200px;top:0;width:345px;height:308px" role="img" aria-label="Photo of a desk with a syringe tray, report clipboard, stethoscope, glasses and phone"></div>
</section>

<!-- Slide: two text columns -->
<section class="slide" style="left:240px;top:772px">
  <div class="rule" style="left:27px;height:66px"></div>
  <div class="accent" style="left:26px;top:36px"></div>
  <div class="title" style="left:43px;top:33px"><span class="kicker">Place for the</span><span class="main">Slide Title</span></div>
  <div class="copy" style="left:43px;top:72px;width:232px;line-height:14px"><p>We plan, build and support clinical systems for hospitals across the region. Our teams cover data centers, networks, medical records, lab and pharmacy software, with on-site training and care for every install. Each project follows clear steps from first review to final handover, and we stay close after go-live. Support staff remain on call to keep every system stable, safe and ready for daily clinical work.</p><p style="margin-top:6px">Training sessions help nurses, doctors and pharmacists use new tools with confidence from the first day.</p></div>
  <div class="copy" style="left:291px;top:72px;width:230px;line-height:14px"><p>We plan, build and support clinical systems for hospitals across the region. Our teams cover data centers, networks, medical records, lab and pharmacy software, with on-site training and care for every install. Each project follows clear steps from first review to final handover, and we stay close after go-live. Support staff remain on call to keep every system stable, safe and ready for daily clinical work.</p><p style="margin-top:6px">Training sessions help nurses, doctors and pharmacists use new tools with confidence from the first day.</p></div>
  <div class="footer" style="left:0;width:545px">
    <div class="brand"><b>BMV</b><small>Bright Medical Ventures</small></div>
    <div class="partner"><i></i>PARTNER LOGO</div>
    <div class="pill">01</div>
  </div>
</section>

<!-- Slide: text with photo strip -->
<section class="slide" style="left:825px;top:772px">
  <div class="rule" style="left:26px;height:160px"></div>
  <div class="accent" style="left:25px;top:89px"></div>
  <div class="title" style="left:38px;top:86px"><span class="kicker">Place for the</span><span class="main">Slide Title</span></div>
  <div class="copy" style="left:232px;top:76px;width:245px">Our specialists link hospital systems into one secure flow of patient data, so care teams see the right record at the right time. Support staff remain on call to keep every system stable, safe and ready for daily clinical work.</div>
  <div class="photo" style="left:224px;top:166px;width:123px;height:118px" role="img" aria-label="Photo of a report beside a laptop"></div>
  <div class="photo" style="left:353px;top:166px;width:192px;height:118px" role="img" aria-label="Photo of medical tools, clipboard and stethoscope"></div>
  <div class="footer" style="left:0;width:545px">
    <div class="brand"><b>BMV</b><small>Bright Medical Ventures</small></div>
    <div class="partner"><i></i>PARTNER LOGO</div>
    <div class="pill">01</div>
  </div>
</section>

<!-- Slide: two photos -->
<section class="slide" style="left:240px;top:1123px">
  <div class="rule" style="left:53px;height:130px"></div>
  <div class="accent" style="left:52px;top:60px"></div>
  <div class="title" style="left:65px;top:57px"><span class="kicker">Place for the</span><span class="main">Slide Title</span></div>
  <div class="photo" style="left:66px;top:122px;width:145px;height:140px" role="img" aria-label="Photo of a clipboard with a syringe tray"></div>
  <div class="photo" style="left:235px;top:26px;width:310px;height:140px" role="img" aria-label="Photo of surgical tools, a report clipboard and stethoscope"></div>
  <div class="copy" style="left:235px;top:176px;width:290px">Our specialists link hospital systems into one secure flow of patient data, so care teams see the right record at the right time. Support staff remain on call to keep every system stable, safe and ready for daily clinical work.</div>
  <div class="footer" style="left:0;width:545px">
    <div class="brand"><b>BMV</b><small>Bright Medical Ventures</small></div>
    <div class="partner"><i></i>PARTNER LOGO</div>
    <div class="pill">01</div>
  </div>
</section>

<!-- Slide: three features -->
<section class="slide" style="left:825px;top:1123px">
  <div class="rule" style="left:26px;height:106px"></div>
  <div class="accent" style="left:25px;top:32px"></div>
  <div class="title" style="left:38px;top:30px"><span class="kicker">Place for the</span><span class="main">Slide Title</span></div>

  <div class="feature" style="left:158px">
    <svg width="80" height="72" viewBox="0 0 80 72">
      <rect x="22" y="6" width="36" height="36" fill="#fff" transform="rotate(45 40 24)" style="filter:drop-shadow(0 2px 3px rgba(0,0,0,.12))"/>
      <polyline points="10,37 40,67 70,37" fill="none" stroke="#1d2842" stroke-width="2.5"/>
      <path d="M35 34 L43 26" stroke="#1d2842" stroke-width="3" stroke-linecap="round"/>
      <circle cx="45" cy="24" r="4" fill="none" stroke="#1d2842" stroke-width="2.5"/>
    </svg>
    <h4>Your Title</h4>
    <p>Short note on this service line for hospital staff and teams.</p>
  </div>
  <div class="feature" style="left:289px">
    <svg width="80" height="72" viewBox="0 0 80 72">
      <rect x="22" y="6" width="36" height="36" fill="#fff" transform="rotate(45 40 24)" style="filter:drop-shadow(0 2px 3px rgba(0,0,0,.12))"/>
      <polyline points="10,37 40,67 70,37" fill="none" stroke="#1d2842" stroke-width="2.5"/>
      <circle cx="40" cy="22" r="4" fill="#1d2842"/>
      <path d="M33 33 Q33 27 40 27 Q47 27 47 33 Z" fill="#1d2842"/>
    </svg>
    <h4>Your Title</h4>
    <p>Short note on this service line for hospital staff and teams.</p>
  </div>
  <div class="feature" style="left:420px">
    <svg width="80" height="72" viewBox="0 0 80 72">
      <rect x="22" y="6" width="36" height="36" fill="#fff" transform="rotate(45 40 24)" style="filter:drop-shadow(0 2px 3px rgba(0,0,0,.12))"/>
      <polyline points="10,37 40,67 70,37" fill="none" stroke="#1d2842" stroke-width="2.5"/>
      <path d="M32 27 H48 M40 27 L44 23 M38 27 L41 31" stroke="#1d2842" stroke-width="1.6" fill="none"/>
      <circle cx="31" cy="27" r="2" fill="#1d2842"/>
      <rect x="44" y="21" width="3" height="3" fill="#1d2842"/>
    </svg>
    <h4>Your Title</h4>
    <p>Short note on this service line for hospital staff and teams.</p>
  </div>

  <div class="footer" style="left:0;width:545px">
    <div class="brand"><b>BMV</b><small>Bright Medical Ventures</small></div>
    <div class="partner"><i></i>PARTNER LOGO</div>
    <div class="pill">01</div>
  </div>
</section>

</div>
</body>
</html>
```